Automotive component supplier needs a business card design

We need a business card design for our company called Velran Global Components Ltd based in the UK. We are a supplier of interior and exterior components to premium car manufacturers such as Corvel Ashby, Hadley Fenn, Marquist and Tavarelli. We would like to see a modern business card design that uses the colour blue.

Target Market(s)

Premium automotive car manufacturers.

Industry/Entity Type

Automotive

Contact Information for Business Card

Company Name : Velran Global Components Limited
Address: 17 Marlow Yard, Upper Heath, Warwick, CV31 8QL, United Kingdom
Web Address : www.velrancomponents-example.co.uk

Font styles to use
Other font styles liked:
• Helvetica

Colors
3176b5
0255a3
85acd3
cfdeed
cee9f5
85cae6
34a6d7
0692cd
9bcb3c

Requirements
Must have
• Clear company logo and a mixture of blue colours.
Nice to have
• A high quality modern image.
Should not have
• Multiple colours.

```html
<!DOCTYPE html>
<html lang="en">
<head>
<meta charset="utf-8">
<title>Velran Global Components – Business Card</title>
<link href="https://fonts.googleapis.com/css2?family=Open+Sans:wght@400;600;700&display=swap" rel="stylesheet">
<style>
  :root {
    --brand-green: #9bcb3c;
    --brand-blue: #0692cd;
    --logo-blue: #0a8fcf;
    --paper-white: #fbfbfb;
    --ink-white: #ffffff;
    --backdrop: #e9ecef;
    --card-shadow: rgba(0, 0, 0, 0.18);
  }
  * { box-sizing: border-box; margin: 0; padding: 0; }
  html, body {
    width: 1200px;
    height: 900px;
    overflow: hidden;
  }
  body {
    background: var(--backdrop);
    font-family: "Open Sans", Helvetica, Arial, sans-serif;
    position: relative;
  }
  .card {
    position: absolute;
    left: 250px;
    width: 700px;
    height: 400px;
    overflow: hidden;
    box-shadow: 0 8px 24px var(--card-shadow);
  }
  .card--front { top: 40px; background: var(--brand-green); }
  .card--back { top: 470px; background: var(--paper-white); }

  .brand {
    position: absolute;
    left: 0;
    right: 0;
    display: flex;
    justify-content: center;
    align-items: center;
    gap: 14px;
    color: var(--logo-blue);
    font-weight: 700;
    font-size: 40px;
    letter-spacing: 0.5px;
  }
  .brand__mark {
    width: 18px;
    height: 18px;
    background: var(--ink-white);
  }
  .card--front .brand { top: 140px; }
  .card--back .brand { top: 80px; }
  .card--back .brand__mark { background: var(--brand-green); }

  .front__web {
    position: absolute;
    left: 0;
    right: 0;
    top: 318px;
    text-align: center;
    color: var(--ink-white);
    font-size: 17px;
    font-weight: 600;
  }

  .back__rule {
    position: absolute;
    left: 0; right: 0;
    top: 222px;
    height: 6px;
    background: var(--brand-green);
  }
  .back__band {
    position: absolute;
    left: 0; right: 0;
    top: 228px;
    bottom: 0;
    background: var(--brand-blue);
    color: var(--ink-white);
  }
  .person {
    position: absolute;
    right: 360px;
    top: 30px;
    text-align: right;
  }
  .person__name { font-size: 22px; font-weight: 700; line-height: 1.2; }
  .person__role { font-size: 18px; font-weight: 400; line-height: 1.3; }
  .divider {
    position: absolute;
    left: 354px;
    top: 18px;
    width: 1px;
    height: 74px;
    background: var(--ink-white);
  }
  .contacts {
    position: absolute;
    left: 372px;
    top: 16px;
    list-style: none;
    font-size: 16px;
    line-height: 26px;
  }
  .contacts li { display: flex; align-items: center; gap: 10px; }
  .contacts svg { width: 14px; height: 14px; fill: var(--ink-white); flex: none; }
  .address {
    position: absolute;
    left: 30px;
    bottom: 22px;
    font-size: 19px;
  }
</style>
</head>
<body>

<section class="card card--front" aria-label="Card front">
  <div class="brand"><span class="brand__mark"></span><span>Velran Global Components</span></div>
  <p class="front__web">www.velrancomponents-example.co.uk</p>
</section>

<section class="card card--back" aria-label="Card back">
  <div class="brand"><span class="brand__mark"></span><span>Velran Global Components</span></div>
  <div class="back__rule"></div>
  <div class="back__band">
    <div class="person">
      <p class="person__name">Elliot Marsh</p>
      <p class="person__role">Managing Director</p>
    </div>
    <div class="divider"></div>
    <ul class="contacts">
      <li>
        <svg viewBox="0 0 16 16" aria-hidden="true"><path d="M1 5c0-2 2-3 7-3s7 1 7 3v1h-4V4.5H5V6H1z M3 7h10l1.5 7h-13z M8 9a2 2 0 1 0 0.01 0z"/></svg>
        (044) 170 555 0142
      </li>
      <li>
        <svg viewBox="0 0 16 16" aria-hidden="true"><path d="M4 1h8v14H4z M5.5 3v9h5V3z M7.2 13h1.6v1H7.2z"/></svg>
        (044)1705550198
      </li>
      <li>
        <svg viewBox="0 0 16 16" aria-hidden="true"><path d="M1 3h14v10H1z M2 4.2v.6l6 4 6-4v-.6z"/></svg>
        hello@velran-mail.example
      </li>
    </ul>
    <p class="address">17 Marlow Yard, Upper Heath, Warwick, CV31 8QL, United Kingdom</p>
  </div>
</section>

</body>
</html>
```